Classy, Elegant, Simple Business Card Design

Looking to have a classy, simple, and elegant design. Want a top notch designed business card. I really like the look of the new torvane credit card. I also like the design I attached. I am trying to reach 21-29 year old females for booking us for there wedding or event. We offer Disc Jockey Service, Photo Booth Rentals, and Uplighting .

Target Market(s)

21-28 year old females

Contact Information for Business Card

Has to have logo, website, email, and phone number

Font styles to use
Other font styles liked:
• open to font choice, modern, clean
Designer to choose
33a6d7
0791cd
0555a3
ffffff

Requirements
Must have
• Has to have logo, website, email, and phone number
Nice to have
• I really like the design of the new torvane credit card. I also included my logo and some designs I like
Should not have
• clutter or too much info

```html
<!DOCTYPE html>
<html lang="en">
<head>
<meta charset="utf-8">
<title>Tidewell Event Group – Business Card</title>
<link rel="stylesheet" href="https://fonts.googleapis.com/css2?family=Lato:wght@400;700&display=swap">
<style>
  :root {
    --bg: #d9d9d9;
    --card-light: #ffffff;
    --card-mid: #efefef;
    --card-edge: #dcdcdc;
    --ink: #2b2b2b;
    --ink-soft: #6f6f6f;
    --brand-sky: #33a6d7;
    --brand-blue: #0791cd;
    --brand-deep: #0555a3;
    --icon: #1f3550;
  }
  * { margin: 0; padding: 0; box-sizing: border-box; }
  html, body { width: 1200px; height: 802px; overflow: hidden; }
  body {
    background: var(--bg);
    font-family: "Lato", sans-serif;
    position: relative;
  }
  .card {
    position: absolute;
    top: 274px;
    width: 434px;
    height: 264px;
    border-radius: 14px;
    background: radial-gradient(ellipse at 55% 55%, var(--card-light) 0%, var(--card-mid) 60%, var(--card-edge) 100%);
    box-shadow: 0 2px 6px rgba(0,0,0,0.18);
  }
  .card--front { left: 138px; }
  .card--back { left: 626px; }

  .brand-name {
    position: absolute;
    left: 26px;
    top: 70px;
    width: 190px;
    color: var(--brand-blue);
    font-weight: 400;
    font-size: 22px;
    line-height: 1.25;
    letter-spacing: 0.5px;
    text-align: center;
  }
  .contact-list {
    position: absolute;
    left: 26px;
    top: 188px;
    list-style: none;
    color: var(--ink);
    font-size: 15px;
  }
  .contact-list li {
    display: flex;
    align-items: center;
    gap: 4px;
    height: 20px;
  }
  .contact-list svg { width: 15px; height: 15px; flex: none; }

  .service-list {
    position: absolute;
    right: 18px;
    top: 188px;
    list-style: none;
    color: var(--ink);
    font-size: 15px;
    text-align: right;
  }
  .service-list li {
    display: flex;
    align-items: center;
    justify-content: flex-end;
    gap: 6px;
    height: 20px;
  }
  .service-list li::after {
    content: "";
    width: 7px;
    height: 7px;
    border-radius: 50%;
    background: var(--brand-blue);
  }

  .back-name {
    position: absolute;
    left: 0;
    right: 0;
    top: 100px;
    text-align: center;
    color: var(--ink-soft);
    font-weight: 400;
    font-size: 34px;
    line-height: 1.15;
    letter-spacing: 2px;
  }
  .back-name .sub {
    display: block;
    font-size: 20px;
    letter-spacing: 8px;
  }
</style>
</head>
<body>
  <section class="card card--front">
    <div class="brand-name">Tidewell<br>Event Group</div>

    <ul class="contact-list">
      <li>
        <svg viewBox="0 0 16 16" aria-hidden="true"><circle cx="8" cy="8" r="8" fill="var(--icon)"/><path d="M4.5 9.5h7v2h-7z M5 7.5c1-2 5-2 6 0l-1 1h-4z" fill="#fff"/></svg>
        044-555 210 384
      </li>
      <li>
        <svg viewBox="0 0 16 16" aria-hidden="true"><circle cx="8" cy="8" r="8" fill="var(--icon)"/><rect x="4" y="5" width="8" height="6" rx="1" fill="#fff"/><path d="M4.3 5.4 8 8.4l3.7-3" stroke="var(--icon)" stroke-width="1" fill="none"/></svg>
        hello@tidewellevents.com
      </li>
      <li>
        <svg viewBox="0 0 16 16" aria-hidden="true"><circle cx="8" cy="8" r="8" fill="var(--icon)"/><circle cx="8" cy="8" r="3.8" fill="none" stroke="#fff" stroke-width="1.2"/><path d="M4.2 8h7.6M8 4.2v7.6" stroke="#fff" stroke-width="1"/></svg>
        www.tidewellevents.com
      </li>
    </ul>

    <ul class="service-list">
      <li>Disc Jockey Service</li>
      <li>Photo Booth Rentals</li>
      <li>Uplighting</li>
    </ul>
  </section>

  <section class="card card--back">
    <div class="back-name">TIDEWELL<span class="sub">EVENT GROUP</span></div>
  </section>
</body>
</html>
```